Financial Advisor Resource Firm needs business card design

Need business card design for company in Omaha NE called Meridale Circle. We provide resources to financial advisors....workshop programs, retirement analysis, and insurance planning. I would like to see designs that use grays, greens, black, and white colors. The final design should communicate 'collaboration' and be simple yet attractive to financial planning clients. I will attached our logo and another picture of a puzzle piece coming together. I would like the incorporate the puzzle picture somehow, maybe on the back somehow, with color or just the gray scale....OR, the picture be the front of the card with 'Meridale' definition on it (see upload) and then company logo, employee name, title, address on the back (see ppt uploaded). The following disclosure needs to be included somewhere- Advisory services offered through Stonebrook Assets, LLC.
Updates

I uploaded a svg and ai file of the logo

Target Market(s)

Financial planning clients and financial advisors....so pretty diverse age range of about 40-70.

Industry/Entity Type

Financial Planning

Contact Information for Business Card

Tobias L. Fenwright, MBA
Founder/President
5287 E. Larkin Road
Suite 230
Omaha, NE 68190
Phone- (402) 555-0147
Cell- (402) 555-0183
Fax- (402) 555-0129
email- tobias@meridaleplan.example
web address- www.meridaleplan.example

Colors
1b1b1b
474747
d3d3d3
ffffff
9bcb3c
abd036

Requirements
Must have
• Must include logo provided, must be 2 sided, and must have disclosure...all of these items listed in project description

```html
<!DOCTYPE html>
<html lang="en">
<head>
<meta charset="utf-8">
<title>Meridale Circle — Business Card</title>
<link rel="stylesheet" href="https://fonts.googleapis.com/css2?family=Roboto:wght@400;500&display=swap">
<style>
  :root {
    --ink: #1b1b1b;
    --graphite: #474747;
    --mist: #d3d3d3;
    --paper: #ffffff;
    --leaf: #9bcb3c;
    --lime: #abd036;
    --backdrop: #f3f3f3;
  }
  * { margin: 0; padding: 0; box-sizing: border-box; }
  html, body { width: 1200px; height: 900px; overflow: hidden; }
  body {
    background: var(--backdrop);
    font-family: "Roboto", Arial, sans-serif;
    position: relative;
  }
  .card {
    position: absolute;
    left: 288px;
    width: 624px;
    height: 356px;
    box-shadow: 0 18px 30px rgba(0,0,0,0.28);
  }
  .card--front { top: 66px; background: var(--ink); }
  .card--back { top: 475px; background: var(--paper); }

  .wordmark {
    position: absolute;
    text-align: right;
    font-weight: 500;
    letter-spacing: 1px;
    line-height: 1;
  }
  .wordmark__dot {
    display: inline-block;
    width: 12px; height: 12px;
    border-radius: 50%;
    background: var(--leaf);
    margin-right: 8px;
    vertical-align: middle;
  }
  .card--front .wordmark { left: 36px; top: 136px; width: 240px; font-size: 23px; color: var(--paper); }
  .card--back .wordmark { left: 46px; top: 168px; width: 218px; font-size: 21px; color: var(--graphite); }

  .tagline {
    position: absolute;
    right: 348px;
    top: 189px;
    text-align: right;
    color: var(--paper);
    font-size: 14.5px;
    line-height: 20px;
  }
  .tagline em { font-style: normal; color: var(--leaf); }

  .photo-frame { position: absolute; left: 326px; top: 22px; width: 274px; height: 318px; }
  .photo-frame__accent { position: absolute; left: 12px; top: 0; width: 261px; height: 302px; background: var(--leaf); }
  .photo-frame__image {
    position: absolute; left: 6px; top: 6px; width: 261px; height: 303px;
    background: linear-gradient(160deg, #f4f8f4 0%, #c9e3c6 30%, #7fbf6c 62%, #2f8f3a 100%);
  }
  .photo-frame__corner { position: absolute; left: 0; top: 0; width: 274px; height: 318px; }

  .contact { position: absolute; left: 312px; top: 60px; color: var(--graphite); }
  .contact__name { font-size: 22px; font-weight: 500; color: var(--leaf); line-height: 26px; }
  .contact__cred { font-size: 14px; color: var(--graphite); font-weight: 400; }
  .contact__title { font-size: 14px; line-height: 20px; }
  .contact__address { margin-top: 10px; font-size: 15px; line-height: 20px; color: var(--leaf); }
  .contact__list { list-style: none; margin-top: 7px; }
  .contact__item { display: flex; align-items: center; height: 25px; font-size: 15.5px; }
  .contact__icon { width: 20px; height: 18px; margin-right: 11px; fill: var(--leaf); }
  .contact__item .hl { color: var(--leaf); }

  .disclosure {
    position: absolute;
    left: 0;
    right: 0;
    bottom: 14px;
    text-align: center;
    font-size: 10px;
    line-height: 12px;
    color: var(--graphite);
    letter-spacing: 0.2px;
  }
</style>
</head>
<body>

<section class="card card--front">
  <div class="wordmark"><span class="wordmark__dot"></span>MERIDALE CIRCLE</div>
  <p class="tagline">To come <em>TOGETHER</em> and <em>UNITE</em><br>in common interest and <em>FOCUS</em></p>

  <div class="photo-frame">
    <div class="photo-frame__accent"></div>
    <div class="photo-frame__image" role="img" aria-label="Photo of hands joining puzzle pieces, tinted green"></div>
    <svg class="photo-frame__corner" viewBox="0 0 274 318" aria-hidden="true">
      <polyline points="1,186 1,316 128,316" fill="none" stroke="#ffffff" stroke-width="1.2"/>
    </svg>
  </div>
</section>

<section class="card card--back">
  <div class="wordmark"><span class="wordmark__dot"></span>MERIDALE CIRCLE</div>

  <div class="contact">
    <h1 class="contact__name">Tobias L. Fenwright<span class="contact__cred">, MBA</span></h1>
    <p class="contact__title">Founder | President</p>
    <p class="contact__address">5287 E. Larkin Road<br>Suite 230, Omaha, NE 68190</p>
    <ul class="contact__list">
      <li class="contact__item">
        <svg class="contact__icon" viewBox="0 0 20 20"><path d="M5 2l3 4-2 2c1 2 3 4 5 5l2-2 4 3-2 3C9 17 3 11 2 5z"/></svg>
        (402) 555 - 0147</li>
      <li class="contact__item">
        <svg class="contact__icon" viewBox="0 0 20 20"><path d="M6 1h8a1 1 0 011 1v16a1 1 0 01-1 1H6a1 1 0 01-1-1V2a1 1 0 011-1zm1 2v12h6V3zm3 13a1 1 0 100 2 1 1 0 000-2z"/></svg>
        (402) 555 - 0183</li>
      <li class="contact__item">
        <svg class="contact__icon" viewBox="0 0 20 20"><path d="M2 6h3v12H2zM6 4h6v4h6v10H6zm2 6v2h2v-2zm4 0v2h2v-2zm-4 4v2h2v-2zm4 0v2h2v-2zM8 1h3v2H8z"/></svg>
        (402) 555 - 0129</li>
      <li class="contact__item">
        <svg class="contact__icon" viewBox="0 0 20 20"><path d="M1 4h18v1l-9 6-9-6zm0 3l9 6 9-6v9H1z"/></svg>
        tobias@meridaleplan.example</li>
      <li class="contact__item">
        <svg class="contact__icon" viewBox="0 0 20 20"><circle cx="10" cy="10" r="8.5"/><path d="M6 5c2 1 1 3 3 3s1 3-1 3-1 3 0 4M13 4c-1 2 1 3 3 3M12 12c2 0 3 1 3 3" fill="none" stroke="#fff" stroke-width="1.4"/></svg>
        www.<span class="hl">meridaleplan</span>.example</li>
    </ul>
  </div>

  <p class="disclosure">Advisory services offered through Stonebrook Assets, LLC.</p>
</section>

</body>
</html>
```